IT Company requires new Business Card design.

Over the years we have had a few different business card designs. We are now due for new cards across the board for all staff. We felt this would be a good time to start fresh with a new design. Our traditional card simply had our details on the front, and a list of services on the back. We don't particularly need the list of services, we have had cards where the only thing on the rear of the card was our logo.
Feel free to be creative, we would like our tag line "Complete IT Management" to appear at some point, doesn't necessarily have to be with the logo.
I have attached samples and drafts of various previous cards we have used over the years.

```html
<!DOCTYPE html>
<html lang="en">
<head>
<meta charset="UTF-8">
<title>Harbor Netlink Business Cards</title>
<link href="https://fonts.googleapis.com/css2?family=Open+Sans:wght@400;600;700;800&display=swap" rel="stylesheet">
<style>
  :root {
    --backdrop: #4b3125;
    --card-light: #f2f3f4;
    --card-mid: #d9dcde;
    --card-dark: #c6cacd;
    --brand: #5f6e79;
    --band: #66747f;
    --text-dark: #4a4f54;
    --white: #ffffff;
  }
  * { margin: 0; padding: 0; box-sizing: border-box; }
  html, body { width: 1034px; height: 1200px; overflow: hidden; }
  body {
    background: var(--backdrop);
    font-family: "Open Sans", Arial, sans-serif;
    position: relative;
  }
  .card {
    position: absolute;
    left: 72px;
    width: 899px;
    height: 510px;
    overflow: hidden;
    background: linear-gradient(150deg, var(--card-mid) 0%, var(--card-light) 35%, var(--card-dark) 55%, var(--card-light) 78%, var(--card-mid) 100%);
    box-shadow: 0 6px 18px rgba(0,0,0,0.45);
  }
  .card--front { top: 63px; }
  .card--back { top: 612px; }

  .brand { position: absolute; display: flex; align-items: flex-start; }
  .brand__mark { background: var(--brand); flex: none; }
  .brand__name {
    color: var(--brand);
    font-weight: 800;
    line-height: 0.95;
    text-transform: uppercase;
  }
  .card--front .brand { left: 185px; top: 45px; }
  .card--front .brand__mark { width: 160px; height: 160px; margin-right: 30px; }
  .card--front .brand__name { padding-top: 24px; }
  .brand__line--big { display: block; font-size: 72px; letter-spacing: -1px; }
  .brand__line--small { display: block; font-size: 52px; letter-spacing: -0.5px; }

  .address {
    position: absolute; top: 253px; left: 0; width: 100%;
    text-align: center; font-size: 22px; color: var(--text-dark);
  }
  .contact-band {
    position: absolute; left: 0; top: 297px; width: 100%; height: 213px;
    background: var(--band); color: var(--white);
    padding: 18px 0 0 62px;
  }
  .person { font-size: 24px; font-weight: 700; margin-bottom: 12px; }
  .person__role { font-weight: 400; font-size: 21px; }
  .contact-list { list-style: none; }
  .contact-list li {
    display: flex; align-items: center; font-size: 21px;
    height: 36px;
  }
  .contact-list svg { width: 20px; height: 20px; margin-right: 10px; flex: none; }
  .contact-list .gap { margin-left: 14px; }

  .card--back .brand { left: 173px; top: 168px; }
  .card--back .brand__mark { width: 155px; height: 155px; margin-right: 45px; }
  .card--back .brand__name { padding-top: 6px; }
  .tagline {
    display: block; margin-top: 10px;
    font-size: 21px; font-weight: 600; letter-spacing: 4.5px;
  }
  .web {
    position: absolute; top: 456px; left: 0; width: 100%;
    text-align: center; font-size: 24px; letter-spacing: 2px;
    color: var(--text-dark);
  }
  .web strong { color: var(--brand); font-weight: 700; }
</style>
</head>
<body>

<section class="card card--front">
  <div class="brand">
    <div class="brand__mark"></div>
    <div class="brand__name">
      <span class="brand__line--big">Harbor</span>
      <span class="brand__line--small">Netlink</span>
    </div>
  </div>
  <p class="address">Unit 7 18 Coral Bay Road, Kelmscott WA 6111</p>
  <div class="contact-band">
    <p class="person">Marcus Hale, <span class="person__role">Operation Manager</span></p>
    <ul class="contact-list">
      <li>
        <svg viewBox="0 0 20 20"><path fill="#fff" d="M5 2l3 4-2 2c1 2.5 3 4.5 6 6l2-2 4 3-2 3C9 18 2 11 2 4z"/></svg>
        08 9521 4870
        <svg class="gap" viewBox="0 0 20 20"><rect x="5" y="1" width="10" height="18" rx="2" fill="#fff"/><rect x="7" y="4" width="6" height="7" fill="#66747f"/></svg>
        0412 508 963
      </li>
      <li>
        <svg viewBox="0 0 20 20"><rect x="5" y="2" width="10" height="6" fill="#fff"/><rect x="2" y="8" width="16" height="8" rx="1" fill="#fff"/><rect x="5" y="13" width="10" height="5" fill="#fff" stroke="#66747f"/></svg>
        08 9521 4870
      </li>
      <li>
        <svg viewBox="0 0 20 20"><rect x="2" y="5" width="16" height="11" rx="1" fill="#fff"/><path d="M2 6l8 6 8-6" fill="none" stroke="#66747f" stroke-width="1.5"/></svg>
        marcus@harbornetlink.com.au
      </li>
      <li>
        <svg viewBox="0 0 20 20"><circle cx="10" cy="10" r="8" fill="none" stroke="#fff" stroke-width="1.6"/><ellipse cx="10" cy="10" rx="3.5" ry="8" fill="none" stroke="#fff" stroke-width="1.4"/><path d="M2 10h16M4 6h12M4 14h12" stroke="#fff" stroke-width="1.2"/></svg>
        www.harbornetlink.com.au
      </li>
    </ul>
  </div>
</section>

<section class="card card--back">
  <div class="brand">
    <div class="brand__mark"></div>
    <div class="brand__name">
      <span class="brand__line--big">Harbor</span>
      <span class="brand__line--small">Netlink</span>
      <span class="tagline">COMPLETE IT MANAGEMENT</span>
    </div>
  </div>
  <p class="web">www.<strong>harbornetlink</strong>.com.au</p>
</section>

</body>
</html>
```